Product Label Design

Need a product design for our Epsom salt product, needs to have a luxurious simple feel to it. The picture attached is our brand and wordage on it, the bag we think should be a stand up bag that should be offwhite/creme color. The other picture are products that we like. We updated the packaging to be a Kraft tube box, please see the attached photo for dimensions.

```html
<!DOCTYPE html>
<html lang="en">
<head>
<meta charset="utf-8">
<title>Nova Revive – Epsom Salt Tube Label</title>
<link rel="stylesheet" href="https://fonts.googleapis.com/css2?family=Montserrat:wght@500;600;700;800&display=swap">
<style>
  :root {
    --backdrop: #f6e6b8;
    --kraft: #f0d48e;
    --kraft-edge: #e4c278;
    --ink: #3a3a3a;
    --band: #3a3a3a;
    --band-text: #efe4c6;
  }
  * { margin: 0; padding: 0; box-sizing: border-box; }
  html, body {
    width: 1200px;
    height: 960px;
    overflow: hidden;
    background: var(--backdrop);
    font-family: "Montserrat", sans-serif;
    color: var(--ink);
  }
  .canvas {
    width: 1200px;
    height: 960px;
    display: flex;
    align-items: center;
    justify-content: center;
  }
  .label {
    width: 460px;
    height: 800px;
    background: var(--kraft);
    border: 1px solid var(--kraft-edge);
    display: flex;
    flex-direction: column;
    align-items: center;
    padding-top: 250px;
    text-align: center;
  }
  .brand {
    font-size: 68px;
    font-weight: 700;
    letter-spacing: 2px;
    line-height: 1;
  }
  .variant {
    margin-top: 36px;
    font-size: 34px;
    font-weight: 700;
    letter-spacing: 1px;
    line-height: 1;
  }
  .descriptor {
    margin-top: 30px;
    font-size: 18px;
    font-weight: 600;
    line-height: 1.35;
  }
  .botanicals {
    margin-top: 18px;
    display: flex;
    gap: 28px;
    background: var(--band);
    color: var(--band-text);
    font-size: 18px;
    font-weight: 500;
    padding: 5px 22px;
    border-radius: 4px;
    white-space: nowrap;
  }
  .net-weight {
    margin-top: auto;
    margin-bottom: 70px;
    font-size: 14px;
    font-weight: 700;
    letter-spacing: 0.5px;
  }
</style>
</head>
<body>
  <main class="canvas">
    <section class="label">
      <h1 class="brand">Nova</h1>
      <h2 class="variant">REVIVE</h2>
      <p class="descriptor">US Sourced Pure Epsom Salt<br>(Magnesium Sulfate)</p>
      <p class="botanicals"><span>+ Abies sibirica</span><span>+ Fir Balsam</span></p>
      <p class="net-weight">NET WT. 3LBS (1360g)</p>
    </section>
  </main>
</body>
</html>
```